High-end construction company needs a business card design

We need a modern looking business card that draws people in, is memorable and looks so good people will want to sick it on their fridges.
On the first side what is needed are:
Logo
My name - Tomasz Brelwik
Title - Managing Director
Website - www.varkelt.co.uk
Email - tomasz@varkelt.co.uk
Telephone - 020 5194 6281
Mobile - 07845139072
On the back side was is needed is a list of all the services we provide:
-Kitchen Renovations
-Bathroom Renovations
-House Renovations
-Garage Conversions
-Extensions
-Loft Conversions
-Conservatories
-Carpentry
-Tiling
-Electrical
-Plumbing & Heating
-Bricklaying
-Landscaping
-Decorating
-Plastering
We would like the colours to be the same shades as on the logo with grey or black for the words.
Target Market(s)
Anyone who needs building work done
Contact Information for Business Card
This business card is for a construction company which strives to deliver excellent service and quality.
The look and feel of the card should represent this.
Requirements
Must have
- On the first side what is needed are:
Logo
My name - Tomasz Brelwik
Title - Managing Director
Website - www.varkelt.co.uk
Email - tomasz@varkelt.co.uk
Telephone - 020 5194 6281
Mobile - 07845139072
Nice to have
- Cool looking features

```html
<!DOCTYPE html>
<html lang="en">
<head>
<meta charset="utf-8">
<title>Varkelt Construction Ltd – Business Card</title>
<link rel="stylesheet" href="https://fonts.googleapis.com/css2?family=Montserrat:wght@400;600;700&display=swap">
<style>
  :root {
    --page-bg: #e4e4e4;
    --green-light: #6db83f;
    --green-dark: #46873c;
    --card-white: #f3f3f3;
    --ink-white: #ffffff;
    --ink-grey: #333333;
  }
  * { box-sizing: border-box; margin: 0; padding: 0; }
  html, body { width: 1200px; height: 960px; overflow: hidden; }
  body {
    background: var(--page-bg);
    font-family: "Montserrat", Arial, sans-serif;
    position: relative;
  }
  .card {
    position: absolute;
    left: 326px;
    width: 551px;
    height: 358px;
    overflow: hidden;
  }
  /* Services side */
  .card--services { top: 104px; background: var(--green-light); color: var(--ink-white); }
  .services-list {
    position: absolute;
    left: 43px;
    top: 31px;
    list-style: none;
    font-size: 15px;
    line-height: 19.5px;
    letter-spacing: 0.2px;
  }
  .services-list li::before { content: "•"; margin-right: 6px; }
  .brand {
    position: absolute;
    text-align: center;
    font-weight: 700;
    line-height: 1;
  }
  .brand__name { display: block; font-size: 46px; letter-spacing: 1px; }
  .brand__sub { display: block; font-size: 14.5px; letter-spacing: 2.6px; margin-top: 6px; }
  .brand__mark { display: block; width: 22px; height: 22px; background: currentColor; margin: 0 auto 10px; }
  .card--services .brand { left: 262px; top: 214px; width: 250px; color: var(--ink-white); }

  /* Contact side */
  .card--contact { top: 504px; background: var(--card-white); }
  .contact-shapes { position: absolute; inset: 0; }
  .card--contact .brand { left: 36px; top: 128px; width: 240px; color: var(--green-light); }
  .person {
    position: absolute;
    right: 34px;
    top: 72px;
    text-align: right;
    color: var(--ink-white);
  }
  .person__name { font-size: 18px; font-weight: 700; letter-spacing: 0.5px; }
  .person__title { font-size: 14.5px; font-weight: 400; margin-top: 3px; }
  .contact-list {
    position: absolute;
    right: 34px;
    top: 231px;
    list-style: none;
    text-align: right;
    color: var(--ink-white);
    font-size: 14px;
    line-height: 19.5px;
  }
  .contact-list li { display: flex; justify-content: flex-end; align-items: center; gap: 5px; }
  .contact-list svg { width: 12px; height: 12px; flex: none; }
</style>
</head>
<body>

<section class="card card--services" aria-label="Services side">
  <ul class="services-list">
    <li>Kitchen Renovations</li>
    <li>Bathroom Renovations</li>
    <li>House Renovations</li>
    <li>Garage Conversions</li>
    <li>Plumbing &amp; Heating</li>
    <li>Loft Conversions</li>
    <li>Conservatories</li>
    <li>Extensions</li>
    <li>Carpentry</li>
    <li>Electrical</li>
    <li>Bricklaying</li>
    <li>Landscaping</li>
    <li>Decorating</li>
    <li>Plastering</li>
    <li>Tiling</li>
  </ul>
  <div class="brand">
    <span class="brand__mark"></span>
    <span class="brand__name">VARKELT</span>
    <span class="brand__sub">CONSTRUCTION LTD</span>
  </div>
</section>

<section class="card card--contact" aria-label="Contact side">
  <svg class="contact-shapes" viewBox="0 0 551 358" width="551" height="358" aria-hidden="true">
    <polygon points="221,0 551,0 551,177 328,177" fill="var(--green-light)"/>
    <polygon points="331,182 551,182 551,358 221,358" fill="var(--green-dark)"/>
  </svg>
  <div class="brand">
    <span class="brand__mark"></span>
    <span class="brand__name">VARKELT</span>
    <span class="brand__sub">CONSTRUCTION LTD</span>
  </div>
  <div class="person">
    <p class="person__name">TOMASZ BRELWIK</p>
    <p class="person__title">Managing Director</p>
  </div>
  <ul class="contact-list">
    <li>020 5194 6281
      <svg viewBox="0 0 12 12"><path d="M2.5 1h2l1 2.5-1.3 1a6 6 0 0 0 3.3 3.3l1-1.3L11 7.5v2A1.5 1.5 0 0 1 9.5 11 8.5 8.5 0 0 1 1 2.5 1.5 1.5 0 0 1 2.5 1z" fill="#fff"/></svg>
    </li>
    <li>07845139072
      <svg viewBox="0 0 12 12"><rect x="3" y="0.7" width="6" height="10.6" rx="1" fill="none" stroke="#fff" stroke-width="1.2"/><circle cx="6" cy="9.4" r="0.6" fill="#fff"/></svg>
    </li>
    <li>tomasz@varkelt.co.uk
      <svg viewBox="0 0 12 12"><rect x="0.8" y="2.3" width="10.4" height="7.4" fill="none" stroke="#fff" stroke-width="1.2"/><path d="M1 2.6l5 4 5-4" fill="none" stroke="#fff" stroke-width="1.2"/></svg>
    </li>
    <li>www.varkelt.co.uk
      <svg viewBox="0 0 12 12"><circle cx="6" cy="6" r="5.2" fill="none" stroke="#fff" stroke-width="1.1"/><ellipse cx="6" cy="6" rx="2.3" ry="5.2" fill="none" stroke="#fff" stroke-width="1"/><path d="M1 6h10M2 3.5h8M2 8.5h8" stroke="#fff" stroke-width="0.9"/></svg>
    </li>
  </ul>
</section>

</body>
</html>
```